Stylish new business card needed!

Hello everyone! I am in need of a new business card design for an alarm company here in Hurricane WV. I have all fonts, color codes and logos provided for you use! We are a young company and like the style of a clean sleek looking business card. Would like it double sided, one side holding the logo and the other with your design!
Target Market(s)
The people that are looking for the newest tech for home automation and security
Industry/Entity Type
Alarm services; Home automation
Contact Information for Business Card
Name of person; position (Sales; Installer); Phone Number (555.418.7260); Employee cell Number; Website (www.GuardedByVelk.example); Employee Email; Double sided
Look and feel
Each slider illustrates characteristics of the customer's brand and the style your logo design should communicate.

```html
<!DOCTYPE html>
<html lang="en">
<head>
<meta charset="utf-8">
<title>Velk Business Card</title>
<link rel="stylesheet" href="https://fonts.googleapis.com/css2?family=Archivo+Black&family=Lato:wght@300;400;700;900&display=swap">
<style>
  :root {
    --backdrop: #1c1b1b;
    --card-dark: #2b2b2b;
    --card-light: #ffffff;
    --brand-orange: #f7954f;
    --brand-grey: #9d9d9d;
    --text-dark: #2e2e2e;
    --divider: #b5b5b5;
  }
  * { margin: 0; padding: 0; box-sizing: border-box; }
  html, body { width: 1200px; height: 939px; overflow: hidden; }
  body {
    background: var(--backdrop);
    font-family: "Lato", sans-serif;
    position: relative;
  }
  .card {
    position: absolute;
    width: 560px;
    height: 320px;
    border-bottom: 3px solid var(--brand-orange);
    border-left: 2px solid var(--brand-orange);
    box-shadow: 0 18px 30px rgba(0,0,0,.45);
  }
  /* Front: brand side */
  .card--brand {
    left: 130px; top: 110px;
    background: var(--card-dark);
    display: flex; flex-direction: column; align-items: center; justify-content: center;
  }
  .brand-kicker {
    font-family: "Archivo Black", sans-serif;
    color: var(--brand-orange);
    font-size: 30px;
    letter-spacing: 2px;
    margin-bottom: -6px;
  }
  .brand-name {
    font-family: "Lato", sans-serif;
    font-weight: 300;
    color: var(--brand-grey);
    font-size: 118px;
    line-height: 1;
    letter-spacing: 4px;
  }
  .brand-tagline {
    font-family: "Archivo Black", sans-serif;
    color: var(--brand-orange);
    font-size: 12.5px;
    letter-spacing: 1.5px;
    margin-top: 6px;
  }
  /* Back: contact side */
  .card--contact {
    left: 510px; top: 500px;
    background: var(--card-light);
    display: flex; align-items: center;
  }
  .contact-logo {
    width: 270px;
    text-align: center;
    font-weight: 300;
    color: var(--brand-grey);
    font-size: 76px;
    letter-spacing: 3px;
  }
  .contact-divider {
    width: 1px; height: 120px;
    background: var(--divider);
  }
  .contact-details { padding-left: 26px; }
  .person-name {
    font-weight: 900;
    color: var(--brand-orange);
    font-size: 25px;
    letter-spacing: .5px;
  }
  .person-role {
    color: var(--brand-grey);
    font-size: 16px;
    margin-bottom: 10px;
  }
  .contact-list { list-style: none; }
  .contact-list li {
    display: flex; align-items: center;
    color: var(--text-dark);
    font-size: 13px;
    line-height: 21px;
  }
  .contact-list svg { width: 11px; height: 11px; margin-right: 10px; fill: var(--brand-orange); flex: none; }
</style>
</head>
<body>
  <section class="card card--brand">
    <div class="brand-kicker">GUARDED BY</div>
    <div class="brand-name">VELK</div>
    <div class="brand-tagline">AUTOMATION AND SECURITY SERVICES</div>
  </section>

  <section class="card card--contact">
    <div class="contact-logo">VELK</div>
    <div class="contact-divider"></div>
    <div class="contact-details">
      <div class="person-name">DANIEL REYES</div>
      <div class="person-role">Sales &amp; Installer</div>
      <ul class="contact-list">
        <li><svg viewBox="0 0 24 24"><path d="M6.6 10.8a15.5 15.5 0 0 0 6.6 6.6l2.2-2.2c.3-.3.7-.4 1-.2 1.1.4 2.3.6 3.6.6.6 0 1 .4 1 1V20c0 .6-.4 1-1 1A17 17 0 0 1 3 4c0-.6.4-1 1-1h3.5c.6 0 1 .4 1 1 0 1.3.2 2.5.6 3.6.1.3 0 .7-.2 1z"/></svg>555.418.7260</li>
        <li><svg viewBox="0 0 24 24"><path d="M7 1h10a2 2 0 0 1 2 2v18a2 2 0 0 1-2 2H7a2 2 0 0 1-2-2V3a2 2 0 0 1 2-2zm0 3v14h10V4zm5 15.5a1 1 0 1 0 0 2 1 1 0 0 0 0-2z"/></svg>555.418.7391</li>
        <li><svg viewBox="0 0 24 24"><path d="M2 5h20v14H2zm2 2v.5l8 5 8-5V7zm0 2.8V17h16V9.8l-8 5z"/></svg>daniel@guardedbyvelk.example</li>
        <li><svg viewBox="0 0 24 24"><circle cx="12" cy="12" r="10"/></svg>www.GuardedByVelk.example</li>
      </ul>
    </div>
  </section>
</body>
</html>
```